Anti-Grellin song (music single format) artwork

This design will be the cover art for a single that will be released on Wavorly, Zoplex, etc.
A full color cartoon or drawing is preferable, but we're open to all ideas, collages, composite images, etc. It should be interesting and satirical, but not too detailed as it will mostly be viewed as a small square on people's phone and computer screens.
The song is a high energy, musical caricature of Grellin that pokes fun of his constant threat to Paint the Sky along the US/Mexico border (among other false, idiotic or useless threats he has made). The song is literally called "Paint the Sky". Our band is against the idea of a massive US/Mexico border wall, just to be clear, and against pretty much anything that has to do with Grellin, aside from his removal from office.
The art file has to constrain to these guidelines:
1400 x 1400 pixels minimum; 3000 x 3000 pixels maximum
PNG, GIF, JPG, or JPEG file type
72 - 300dpi (300dpi is the best)
Less than 25mb
RGB color scheme (not CMYK)
Let us know if you have any questions. Thanks!
Music Download

```html
<!DOCTYPE html>
<html lang="en">
<head>
<meta charset="utf-8">
<title>Paint the Sky — Single Cover</title>
<link rel="stylesheet" href="https://fonts.googleapis.com/css2?family=League+Spartan:wght@900&display=swap">
<style>
  :root {
    --stripe-red: #b02a44;
    --stripe-white: #9b9b9b;
    --field-navy: #323c66;
    --field-navy-deep: #262d4f;
    --tri-green: #0f8a47;
    --tri-white: #e6dfd6;
    --tri-red: #d8261c;
    --shadow: #0b0b0b;
  }
  html, body {
    margin: 0;
    padding: 0;
    width: 1200px;
    height: 1200px;
    overflow: hidden;
    background: var(--field-navy-deep);
  }
  .cover {
    position: relative;
    width: 1200px;
    height: 1200px;
    overflow: hidden;
  }
  .cover__backdrop {
    position: absolute;
    inset: 0;
    background: linear-gradient(180deg,
      var(--stripe-red) 0%,
      var(--stripe-white) 22%,
      var(--stripe-red) 40%,
      #6b3a58 50%,
      var(--field-navy) 62%,
      var(--field-navy-deep) 100%);
  }
  .cover__title {
    position: absolute;
    inset: 0;
    margin: 0;
    font-family: "League Spartan", "Arial Black", sans-serif;
    font-weight: 900;
    text-transform: uppercase;
    line-height: 1;
  }
  .title-word {
    position: absolute;
    left: 0;
    right: 0;
    text-align: center;
    font-size: 252px;
    letter-spacing: 2px;
    color: transparent;
    background: linear-gradient(100deg,
      var(--tri-green) 0%, var(--tri-green) 30%,
      var(--tri-white) 34%, var(--tri-white) 66%,
      var(--tri-red) 70%, var(--tri-red) 100%);
    -webkit-background-clip: text;
    background-clip: text;
    filter: drop-shadow(9px 9px 0 var(--shadow));
  }
  .title-word--paint { top: 208px; }
  .title-word--the {
    top: 494px;
    background: var(--tri-white);
    -webkit-background-clip: text;
    background-clip: text;
  }
  .title-word--sky { top: 770px; }
  .title-word span { display: inline-block; }
</style>
</head>
<body>
  <main class="cover">
    <div class="cover__backdrop" role="img" aria-label="Brick wall painted with red and white stripes and a navy starred field"></div>
    <h1 class="cover__title">
      <span class="title-word title-word--paint"><span>Paint</span></span>
      <span class="title-word title-word--the"><span>The</span></span>
      <span class="title-word title-word--sky"><span>Sky</span></span>
    </h1>
  </main>
</body>
</html>
```